Bramwell Lodge Business Cards design with a logo

I want two Business cards designed with a very modern contemporary logo UNING 1920'S FONT STYLES with the following details

Address:
Bramwell Lodge
17 Pellham Road
Helensburgh
G83 2RN

Details for card 1

Name: Dermot Ashby
email: Dermot.ashby@bramwell.lodge
Tel : +971 52 318 6094
Tel +44 7700 900 318

Details Card 2

Name: Dermot Ashby
email: Neville.osgood@bramwell.lodge
Tel : +971 52 430 9187

Bramwell lodge is a house that was built around 1880 and was used extensively in the 1920's for entertaining and parties in the arts scene, the house again will be resurrected to a modern entertainment venue

If you have any questions feel free to ask

Target Market(s)

The market for this is the young modern crowd

Industry/Entity Type

Entertainment Industry

Contact Information for Business Card

Address:
Bramwell Lodge
17 Pellham Road
Helensburgh
G83 2RN

Details for card 1

Name: Dermot Ashby
Tel : +971 52 318 6094
Tel +44 7700 900 318

Details Card 2

Name: Neville Osgood
Tel : +971 52 430 9187

Logo Text

Bramwell Lodge

Font styles to use
Other font styles liked:
• 1920'S FONT STULES

Requirements
Must have
• Modern Contemporary, whilst taking into consideration the age of the house as detailed above. YOU MUT BE USING 1920'S FONT STYLES
Nice to have
• 1920'S FONT STYLES see attached image if a suggestion
Should not have
• Should not look old or dated

```html
<!DOCTYPE html>
<html lang="en">
<head>
<meta charset="utf-8">
<title>Bramwell Lodge – Business Cards</title>
<link rel="stylesheet" href="https://fonts.googleapis.com/css2?family=Montserrat:wght@500;600&family=Work+Sans:wght@400&display=swap">
<style>
  :root {
    --backdrop: #2b2b2b;
    --card: #1d1d1d;
    --card-edge: #262626;
    --accent: #f2d600;
    --ink: #ffffff;
    --ink-soft: #d9d9d9;
  }
  * { margin: 0; padding: 0; box-sizing: border-box; }
  html, body {
    width: 1200px; height: 900px; overflow: hidden;
    background: var(--backdrop);
  }
  .stage {
    width: 1200px; height: 900px;
    display: flex; flex-direction: column; align-items: center; justify-content: center;
    gap: 40px;
  }
  .card {
    position: relative;
    width: 720px; height: 400px;
    background: var(--card);
    border: 1px solid var(--card-edge);
    box-shadow: 0 10px 28px rgba(0,0,0,0.45);
    overflow: hidden;
  }
  /* back side */
  .card-back .pattern-field {
    position: absolute; inset: 0;
    background: linear-gradient(100deg, #1b1b1b 0%, #262626 45%, #3c3c3c 100%);
  }
  .card-back .corner-mark {
    position: absolute; right: 44px; bottom: 62px;
    display: flex; align-items: center; gap: 10px;
    font-family: "Montserrat", sans-serif; font-weight: 600;
    font-size: 20px; color: var(--ink);
  }
  .corner-mark .mark-square {
    width: 18px; height: 18px; background: var(--accent);
  }
  /* front side */
  .card-front .brand-name {
    position: absolute; left: 60px; top: 180px;
    font-family: "Montserrat", sans-serif; font-weight: 500;
    font-size: 30px; line-height: 1; color: var(--ink); letter-spacing: 0.3px;
    white-space: nowrap;
  }
  .card-front .divider {
    position: absolute; left: 384px; top: 96px;
    width: 2px; height: 208px; background: var(--accent);
  }
  .contact {
    position: absolute; left: 410px; top: 92px;
    font-family: "Work Sans", sans-serif; color: var(--ink);
    white-space: nowrap;
  }
  .contact .person-name {
    font-family: "Montserrat", sans-serif; font-weight: 600;
    font-size: 24px; color: var(--accent); line-height: 1.1;
  }
  .contact .person-role {
    font-size: 14px; color: var(--ink-soft); margin-top: 2px; letter-spacing: 0.5px;
  }
  .contact .address {
    font-size: 15px; line-height: 1.4; margin-top: 14px; letter-spacing: 0.5px;
  }
  .contact .lines { list-style: none; margin-top: 12px; }
  .contact .lines li {
    display: flex; align-items: center; gap: 10px;
    font-size: 15px; line-height: 1.45; letter-spacing: 0.5px;
  }
  .contact .lines svg { width: 12px; height: 12px; flex: none; }
  .web-name { color: var(--accent); }
</style>
</head>
<body>
<main class="stage">
  <section class="card card-back" aria-label="Card back">
    <div class="pattern-field" role="img" aria-label="Tonal repeating brand pattern across the card back"></div>
    <div class="corner-mark"><span class="mark-square"></span>Bramwell Lodge</div>
  </section>

  <section class="card card-front" aria-label="Card front">
    <div class="brand-name">Bramwell Lodge</div>
    <div class="divider"></div>
    <div class="contact">
      <div class="person-name">Dermot Ashby</div>
      <div class="person-role">Director</div>
      <div class="address">17 Pellham Road<br>Helensburgh&nbsp; G83 2RN</div>
      <ul class="lines">
        <li>
          <svg viewBox="0 0 12 12"><path d="M2.5 1 L4.5 1 L5 3.5 L3.8 4.5 C4.5 6 6 7.5 7.5 8.2 L8.5 7 L11 7.5 L11 9.5 C11 10.5 10 11 9 10.8 C5 10 2 7 1.2 3 C1 2 1.5 1 2.5 1 Z" fill="#f2d600"/></svg>
          +971 52 318 6094
        </li>
        <li>
          <svg viewBox="0 0 12 12"><path d="M1 4 C1 2 11 2 11 4 L9 5 L8 4 L4 4 L3 5 Z" fill="#f2d600"/><rect x="3" y="6" width="6" height="4.5" rx="0.8" fill="#f2d600"/></svg>
          +44 7700 900 318
        </li>
        <li>
          <svg viewBox="0 0 12 12"><rect x="1" y="2.5" width="10" height="7" fill="none" stroke="#f2d600" stroke-width="1.2"/><path d="M1 2.5 L6 6.5 L11 2.5" fill="none" stroke="#f2d600" stroke-width="1.2"/></svg>
          Dermot.ashby@bramwell.lodge
        </li>
        <li>
          <svg viewBox="0 0 12 12"><circle cx="6" cy="6" r="5" fill="none" stroke="#f2d600" stroke-width="1.1"/><ellipse cx="6" cy="6" rx="2.2" ry="5" fill="none" stroke="#f2d600" stroke-width="1"/><path d="M1 6 H11 M2 3.5 H10 M2 8.5 H10" stroke="#f2d600" stroke-width="0.9"/></svg>
          <span>www.<span class="web-name">bramwelllodge</span>.com</span>
        </li>
      </ul>
    </div>
  </section>
</main>
</body>
</html>
```